Dynamic Business Card for Sports Supplements Company

Hi! I'm looking for an awesome business card to match my existing sports supplement company. I have uploaded my current company logo and screenshot of the front page of my website.

I would like to have something dynamic and interesting and utilize the colors in the website - the reds and purples

The business card should be double sided and focus on a unique eye-catching design on the back and include all the relevant company info.

Most importantly, it should say somewhere: "Sign up on our website for a coupon code."

Target Market(s)

Mostly for women gym goers but it shouldn't be too feminine. It should be in keeping with the website design. It should flow and clearly be connected to it

Industry/Entity Type

Business

Contact Information for Business Card

Lorraine K. Vestal
CEO
LVestal@Quorvanexco.com
www.quorvanexco.com
555.417.3820
P.O. Box 47315
Fenwick Hollow, Westmarch 00000

Sign up on our website for a coupon code

Font styles to use
Serif
Sans Serif
Other font styles liked:
• Novecento font family and "Quorvanex" is in AR Destine font

Requirements
Must have
• One side should be a bold Quorvanex logo design. Even just the symbol itself may be o.k. (see attached file)

```html
<!DOCTYPE html>
<html lang="en">
<head>
<meta charset="utf-8">
<title>Quorvanex Business Card</title>
<link href="https://fonts.googleapis.com/css2?family=Roboto:wght@300;400;900&display=swap" rel="stylesheet">
<style>
  :root{
    --bg:#e9e6e1;
    --card:#121212;
    --card-hi:#232323;
    --red:#e8343c;
    --white:#ffffff;
    --rule:#5c5c5c;
  }
  *{margin:0;padding:0;box-sizing:border-box}
  html,body{width:1200px;height:950px;overflow:hidden;background:var(--bg)}
  body{font-family:"Roboto",Arial,sans-serif;position:relative}
  .card{
    position:absolute;left:250px;width:700px;height:400px;
    background:linear-gradient(135deg,var(--card-hi) 0%,var(--card) 55%,#0a0a0a 100%);
    border-radius:6px;overflow:hidden;color:var(--white);
    box-shadow:0 6px 18px rgba(0,0,0,.25);
  }
  .card-front{top:50px}
  .card-back{top:500px}
  .edge-band{position:absolute;right:0;top:0;width:14px;height:100%;background:var(--red)}
  .brand{display:flex;align-items:center;gap:12px}
  .brand-mark{width:22px;height:22px;background:var(--red)}
  .brand-name{font-weight:900;font-size:34px;letter-spacing:1px;text-transform:uppercase;color:var(--white)}
  .card-front .brand{position:absolute;left:60px;top:60px}
  .divider{position:absolute;left:60px;right:60px;top:150px;height:1px;background:var(--rule)}
  .address{position:absolute;right:60px;top:52px;text-align:right;font-weight:300;font-size:19px;line-height:1.45}
  .person{position:absolute;left:60px;top:190px}
  .person-name{color:var(--red);font-size:26px;font-weight:400}
  .person-role{font-size:16px;font-weight:300;margin-top:4px;margin-bottom:18px}
  .contact-list{list-style:none}
  .contact-list li{display:flex;align-items:center;gap:12px;font-size:17px;font-weight:300;margin-bottom:9px}
  .contact-list svg{width:16px;height:16px;flex:none}
  .card-back .brand{position:absolute;left:50%;top:150px;transform:translateX(-50%)}
  .card-back .brand-name{font-size:54px}
  .card-back .brand-mark{width:34px;height:34px}
  .signup{position:absolute;left:0;right:0;top:265px;text-align:center;font-weight:300;font-size:19px;color:var(--white)}
</style>
</head>
<body>

<section class="card card-front">
  <div class="brand">
    <span class="brand-mark"></span>
    <span class="brand-name">Quorvanex</span>
  </div>
  <div class="address">P.O. Box 47315<br>Fenwick Hollow, Westmarch 00000</div>
  <div class="divider"></div>
  <div class="person">
    <div class="person-name">Lorraine K. Vestal</div>
    <div class="person-role">CEO</div>
    <ul class="contact-list">
      <li>
        <svg viewBox="0 0 16 16"><rect x="1" y="5" width="14" height="10" rx="2" fill="#e8343c"/><path d="M3 6 Q8 0 13 6" stroke="#e8343c" stroke-width="2.2" fill="none"/><circle cx="8" cy="10" r="2" fill="#121212"/></svg>
        555.417.3820
      </li>
      <li>
        <svg viewBox="0 0 16 16"><rect x="1" y="3" width="14" height="10" rx="1.5" fill="#e8343c"/><path d="M1.5 4 L8 9 L14.5 4" stroke="#121212" stroke-width="1.4" fill="none"/></svg>
        LVestal@Quorvanexco.com
      </li>
      <li>
        <svg viewBox="0 0 16 16"><circle cx="8" cy="8" r="7" fill="#e8343c"/><path d="M1 8h14M8 1c-3 3-3 11 0 14M8 1c3 3 3 11 0 14" stroke="#121212" stroke-width="1" fill="none"/></svg>
        www.quorvanexco.com
      </li>
    </ul>
  </div>
  <div class="edge-band"></div>
</section>

<section class="card card-back">
  <div class="brand">
    <span class="brand-mark"></span>
    <span class="brand-name">Quorvanex</span>
  </div>
  <p class="signup">Sign up on our website for a coupon code</p>
</section>

</body>
</html>
```